Landing page design for my current website

I need a landing page designed for my Wordpress website. My website is Velmorquay.com, and I need a page that will serve as a landing page for online ads I run. Please follow the color scheme of the current website

This web page will be targeted towards real estate owners who are looking for a property manager. Above the fold needs to have a CTA form headlined with "As a Rental Property Owner, I Want More Protection, Less Stress, and Drama-Free Living"

A few highlights that can be listed beyond the CTA and fold

- Comprehensive Property Management
Full-service management covering tenant placement, leasing, maintenance, and inspections.

Maximized Rental Income
Proven strategies to optimize rental rates and minimize vacancies, ensuring higher ROI.

Stress-Free Management
We handle all tenant interactions, maintenance requests, and property issues, so you don't have to.

Experienced Team
Over a decade of experience in managing single-family homes, small multifamily units, and apartment complexes.

Advanced Technology
Utilize cutting-edge property management software for efficient communication, rent collection, and maintenance tracking.

Tenant Screening and Placement
Thorough background checks and tenant screening processes to ensure reliable and responsible tenants.

Regular Property Inspections
Routine inspections to maintain property condition and address issues before they become costly problems.

Legal Compliance
Expertise in local and federal rental laws to keep your properties compliant and avoid legal hassles.

Transparent Reporting
Detailed monthly reports and financial statements to keep you informed about your property's performance.

Personalized Service
Tailored management plans to meet the unique needs of your properties and investment goals.
Effective Tenant Conflict Resolution
Skilled in handling challenging tenant situations, ensuring conflicts are resolved quickly and professionally to maintain a peaceful living environment and protect your investment.

```html
<!DOCTYPE html>
<html lang="en">
<head>
<meta charset="utf-8">
<title>Velmorquay Realty – Rental Property Management</title>
<link href="https://fonts.googleapis.com/css2?family=Lato:wght@700;900&family=Roboto:wght@400;500;700&display=swap" rel="stylesheet">
<style>
:root{
  --navy:#0f3f78;
  --dark:#333333;
  --footer:#2f2f2f;
  --text:#333333;
  --muted:#555555;
  --white:#ffffff;
  --line:#555555;
  --soft:#f3f3f3;
}
*{box-sizing:border-box;margin:0;padding:0}
html,body{width:771px;height:1200px;overflow:hidden;background:var(--white);font-family:'Roboto',sans-serif;color:var(--text)}
.page{position:relative;width:771px;height:1200px;overflow:hidden}

.topbar{position:absolute;left:0;top:0;width:771px;height:30px;background:var(--dark)}
.topbar .contact{position:absolute;left:72px;top:5px;display:flex;align-items:center;gap:10px;color:var(--white);font-size:8.6px}
.topbar .ico{width:20px;height:20px;border-radius:50%;background:var(--white);display:flex;align-items:center;justify-content:center}
.topbar .sep{margin:0 3px}
.topbar .social{position:absolute;left:578px;top:0;width:193px;height:30px;background:var(--navy);display:flex;padding-left:49px}
.topbar .social span{width:24px;height:30px;display:flex;align-items:center;justify-content:center;border-left:1px solid rgba(255,255,255,.15);font-size:7px;font-weight:500;color:var(--white)}
.topbar .social span:first-child{background:var(--soft);color:var(--dark)}

.header{position:absolute;left:0;top:30px;width:771px;height:75px}
.brand{position:absolute;left:72px;top:22px;display:flex;align-items:center;gap:8px;font-weight:700;font-size:15px;color:var(--navy);letter-spacing:.5px}
.brand .mark{width:30px;height:30px;border-radius:50%;border:2.5px solid var(--navy)}
.nav{position:absolute;top:33px;left:0;font-size:9.6px;font-weight:500;color:var(--text)}
.nav a{position:absolute;white-space:nowrap;text-decoration:none;color:inherit}
.nav .active{color:var(--navy)}

.hero{position:absolute;left:0;top:105px;width:771px;height:402px;background:linear-gradient(180deg,#c9e0ef 0%,#cfe3ef 35%,#9fb0b9 55%,#8d8a78 72%,#6d7a55 88%,#c9c7bd 100%)}
.hero h1{position:absolute;left:0;top:62px;width:771px;text-align:center;font-family:'Lato',sans-serif;font-weight:900;font-size:24px;line-height:30px;color:var(--dark);letter-spacing:-.3px}
.form{position:absolute;left:108px;top:166px;width:555px;height:79px;background:rgba(160,180,200,.45);border-radius:5px}
.field{position:absolute;height:30px;background:var(--white);border-radius:2px;font-size:8.6px;color:var(--text);padding-left:10px;display:flex;align-items:center}
.field b{color:#d22;font-weight:400;margin-left:3px}
.btn{position:absolute;left:372px;top:43px;width:176px;height:30px;background:var(--navy);color:var(--white);font-weight:500;font-size:9px;display:flex;align-items:center;justify-content:center;border-radius:2px}

.what h2{position:absolute;left:0;top:583px;width:771px;text-align:center;font-family:'Lato',sans-serif;font-weight:700;font-size:25px;color:var(--dark);letter-spacing:-.3px}
.card{position:absolute;top:654px;width:144px;height:237px;background:var(--white);border-radius:12px;box-shadow:0 3px 10px rgba(0,0,0,.1);padding:17px 16px}
.card .badge{width:55px;height:55px;border-radius:50%;background:var(--navy);display:flex;align-items:center;justify-content:center}
.card h3{margin-top:20px;font-size:10.8px;font-weight:500;line-height:16.5px;color:var(--dark)}
.card p{margin-top:5px;font-size:9.6px;line-height:15.4px;color:var(--muted)}
.card.featured{background:var(--navy)}
.card.featured .badge{background:var(--white)}
.card.featured h3,.card.featured p{color:var(--white)}
.arrow{position:absolute;left:724px;width:22px;height:22px;border-radius:50%;display:flex;align-items:center;justify-content:center;box-shadow:0 1px 4px rgba(0,0,0,.15)}

.footer{position:absolute;left:0;top:959px;width:771px;height:241px;background:var(--footer);color:var(--white)}
.footer .brand{left:0;width:771px;justify-content:center;top:34px;color:var(--white)}
.footer .brand .mark{border-color:var(--white)}
.fnav{position:absolute;top:83px;left:0;width:771px;text-align:center;font-size:10.5px;font-weight:700;word-spacing:2px}
.fnav span{margin:0 10px}
.rule{position:absolute;left:72px;width:627px;height:1px;background:var(--line)}
.info{position:absolute;top:127px;display:flex;align-items:center;gap:15px}
.info .circ{width:48px;height:48px;border-radius:50%;background:var(--white);display:flex;align-items:center;justify-content:center;flex:none}
.info h4{font-size:9.4px;font-weight:500;margin-bottom:5px}
.info p{font-size:8.8px;line-height:13px}
.vline{position:absolute;top:120px;width:1px;height:68px;background:var(--line)}
.copy{position:absolute;top:214px;left:0;width:771px;text-align:center;font-size:8px}
.fsocial{position:absolute;top:207px;left:615px;display:flex;gap:5px}
.fsocial span{width:24px;height:24px;border-radius:50%;background:var(--white);display:flex;align-items:center;justify-content:center;font-size:7px;font-weight:500;color:var(--dark)}
.fsocial span:first-child{background:var(--navy);color:var(--white)}
</style>
</head>
<body>
<div class="page">
  <div class="topbar">
    <div class="contact">
      <span class="ico"><svg width="10" height="10" viewBox="0 0 24 24"><path fill="#0f3f78" d="M6.6 10.8a15 15 0 0 0 6.6 6.6l2.2-2.2c.3-.3.7-.4 1-.2 1.1.4 2.3.6 3.6.6.6 0 1 .4 1 1V20c0 .6-.4 1-1 1A17 17 0 0 1 3 4c0-.6.4-1 1-1h3.5c.6 0 1 .4 1 1 0 1.3.2 2.5.6 3.6.1.3 0 .7-.2 1z"/></svg></span>
      <span>555.014.2290</span><span class="sep">|</span>
      <span class="ico"><svg width="10" height="10" viewBox="0 0 24 24"><path fill="#0f3f78" d="M3 6h18v12H3z"/><path d="M3 6l9 7 9-7" stroke="#fff" stroke-width="2" fill="none"/></svg></span>
      <span>hello@Velmorquay.com</span>
    </div>
    <div class="social"><span>Nb</span><span>Qv</span><span>Lm</span></div>
  </div>

  <div class="header">
    <div class="brand"><span class="mark"></span>VELMORQUAY REALTY</div>
    <nav class="nav">
      <a class="active" style="left:393px">HOME</a>
      <a style="left:441px">ABOUT US</a>
      <a style="left:508px">OUR SERVICES</a>
      <a style="left:596px">BLOG</a>
      <a style="left:640px">CONTACT US</a>
    </nav>
  </div>

  <section class="hero" role="img" aria-label="Photo of a suburban street lined with two-storey family houses under a clear sky">
    <h1>AS A RENTAL PROPERTY OWNER,<br>I WANT MORE PROTECTION, LESS STRESS,<br>AND DRAMA-FREE LIVING</h1>
    <div class="form">
      <div class="field" style="left:8px;top:7px;width:176px">Name</div>
      <div class="field" style="left:190px;top:7px;width:176px">Phone</div>
      <div class="field" style="left:372px;top:7px;width:176px">Email<b>*</b></div>
      <div class="field" style="left:8px;top:43px;width:358px">Property Address<b>*</b></div>
      <div class="btn">SEARCH</div>
    </div>
  </section>

  <section class="what">
    <h2>WHAT WE DO</h2>

    <div class="card" style="left:72px">
      <div class="badge"><svg width="26" height="26" viewBox="0 0 24 24"><circle cx="12" cy="12" r="9" fill="none" stroke="#fff" stroke-width="2.5" stroke-dasharray="3 2"/><path d="M7 12l5-4 5 4v5H7z" fill="#fff"/></svg></div>
      <h3>COMPREHENSIVE PROPERTY MANAGEMENT</h3>
      <p>Full-service management covering tenant placement, leasing, maintenance, and inspections.</p>
    </div>
    <div class="card" style="left:233px">
      <div class="badge"><svg width="26" height="26" viewBox="0 0 24 24"><path d="M3 10l9-7 9 7v11H3z" fill="none" stroke="#fff" stroke-width="2"/><rect x="6" y="13" width="12" height="6" fill="#fff"/></svg></div>
      <h3>MAXIMIZED<br>RENTAL INCOME</h3>
      <p>Proven strategies to optimize rental rates and minimize vacancies, ensuring higher ROI.</p>
    </div>
    <div class="card featured" style="left:394px">
      <div class="badge"><svg width="26" height="26" viewBox="0 0 24 24"><circle cx="12" cy="7" r="3" fill="#333"/><path d="M3 15l5-3 4 3 4-3 5 3-5 4h-8z" fill="#333"/></svg></div>
      <h3>STRESS-FREE<br>MANAGEMENT</h3>
      <p>We handle all tenant interactions, maintenance requests, and property issues, so you don't have to.</p>
    </div>
    <div class="card" style="left:555px">
      <div class="badge"><svg width="26" height="26" viewBox="0 0 24 24"><circle cx="8" cy="7" r="2.5" fill="#fff"/><circle cx="16" cy="7" r="2.5" fill="#fff"/><circle cx="12" cy="13" r="4" fill="none" stroke="#fff" stroke-width="2.5"/><path d="M4 12h4M16 12h4" stroke="#fff" stroke-width="2.5"/></svg></div>
      <h3>EXPERIENCED<br>TEAM</h3>
      <p>Over a decade of experience in managing single-family homes, small multifamily units, and apartment complexes.</p>
    </div>

    <div class="arrow" style="top:748px;background:var(--navy)"><svg width="10" height="10" viewBox="0 0 10 10"><path d="M3 1l4 4-4 4" stroke="#fff" stroke-width="1.6" fill="none"/></svg></div>
    <div class="arrow" style="top:775px;background:var(--white)"><svg width="10" height="10" viewBox="0 0 10 10"><path d="M7 1L3 5l4 4" stroke="#333" stroke-width="1.6" fill="none"/></svg></div>
  </section>

  <footer class="footer">
    <div class="brand"><span class="mark"></span>VELMORQUAY REALTY</div>
    <div class="fnav">HOME<span>|</span>ABOUT US<span>|</span>OUR SERVICES<span>|</span>BLOG<span>|</span>CONTACT US</div>
    <div class="rule" style="top:110px"></div>

    <div class="info" style="left:72px">
      <div class="circ"><svg width="22" height="22" viewBox="0 0 24 24"><path d="M12 2a6 6 0 0 1 6 6c0 4.5-6 10-6 10S6 12.5 6 8a6 6 0 0 1 6-6z" fill="#0f3f78"/><circle cx="12" cy="8" r="2.3" fill="#fff"/><ellipse cx="12" cy="20" rx="7" ry="2" fill="none" stroke="#0f3f78" stroke-width="1.6"/></svg></div>
      <div><h4>LOCATION:</h4><p>48 Alder Row, Fenwick<br>PA, 10482</p></div>
    </div>
    <div class="vline" style="left:273px"></div>
    <div class="info" style="left:324px">
      <div class="circ"><svg width="22" height="22" viewBox="0 0 24 24"><path fill="#0f3f78" d="M6.6 10.8a15 15 0 0 0 6.6 6.6l2.2-2.2c.3-.3.7-.4 1-.2 1.1.4 2.3.6 3.6.6.6 0 1 .4 1 1V20c0 .6-.4 1-1 1A17 17 0 0 1 3 4c0-.6.4-1 1-1h3.5c.6 0 1 .4 1 1 0 1.3.2 2.5.6 3.6.1.3 0 .7-.2 1z"/></svg></div>
      <div><h4>PHONE:</h4><p>555.014.2290</p></div>
    </div>
    <div class="vline" style="left:498px"></div>
    <div class="info" style="left:527px">
      <div class="circ"><svg width="22" height="22" viewBox="0 0 24 24"><path d="M3 9l9-6 9 6v11H3z" fill="#0f3f78"/><path d="M3 9l9 6 9-6" stroke="#fff" stroke-width="1.5" fill="none"/></svg></div>
      <div><h4>EMAIL:</h4><p>hello@Velmorquay.com</p></div>
    </div>

    <div class="rule" style="top:198px"></div>
    <div class="copy">© 2024 VELMORQUAY REALTY &nbsp;|&nbsp; All Rights Reserved</div>
    <div class="fsocial"><span>Nb</span><span>Qv</span><span>Lm</span></div>
  </footer>
</div>
</body>
</html>
```